Moravel Aesthetic Doctor

I require an elegant, luxurious looking business card for my aesthetic business. I am a doctor and that will set me aside from competitors. I am planning to provide home and spa based treatments to clients with high expectations. I have attached my logo.

```html
<!DOCTYPE html>
<html lang="en">
<head>
<meta charset="utf-8">
<title>Moravel Aesthetic Doctor – Business Card</title>
<link href="https://fonts.googleapis.com/css2?family=Roboto:wght@300;400;500;700&display=swap" rel="stylesheet">
<style>
  :root {
    --backdrop: #3a3b3d;
    --card: #1f2022;
    --card-edge: #2a2b2e;
    --silver: #b9bec6;
    --sky: #52b3ea;
    --sky-deep: #1f86cf;
    --white: #ffffff;
    --muted: #c9ccd1;
    --stripe: #a9adb5;
  }
  * { margin: 0; padding: 0; box-sizing: border-box; }
  html, body {
    width: 799px; height: 1200px; overflow: hidden;
    background: var(--backdrop);
    font-family: "Roboto", Arial, sans-serif;
  }
  .card {
    position: absolute; left: 40px; width: 719px; height: 411px;
    background: linear-gradient(160deg, var(--card-edge), var(--card) 60%);
    border-radius: 6px; overflow: hidden;
    box-shadow: 0 12px 30px rgba(0,0,0,.45);
  }
  .card--front { top: 110px; }
  .card--back { top: 680px; }

  .brand { position: absolute; display: flex; align-items: center; gap: 22px; }
  .brand__mark {
    width: 96px; height: 96px; border-radius: 50%;
    border: 3px solid var(--silver);
  }
  .brand__name {
    color: var(--silver); font-weight: 300; text-transform: uppercase;
    line-height: 1;
  }
  .brand__name span { display: block; }
  .brand__name .primary { font-size: 64px; letter-spacing: 6px; }
  .brand__name .secondary { font-size: 27px; letter-spacing: 5px; margin-top: 6px; }

  .card--front .brand { left: 90px; top: 60px; }
  .services {
    position: absolute; left: 0; right: 0; top: 200px;
    text-align: center; color: var(--white); font-size: 20px; line-height: 1.45;
  }
  .band {
    position: absolute; left: 0; right: 0; top: 296px; height: 48px;
    background: var(--sky); color: var(--white);
    font-size: 20px; letter-spacing: 1px; text-align: center; line-height: 48px;
  }

  .card--back .brand { left: 70px; top: 36px; }
  .card--back .brand__mark { width: 84px; height: 84px; }
  .card--back .brand__name .primary { font-size: 56px; }
  .card--back .brand__name .secondary { font-size: 24px; }

  .doctor { position: absolute; left: 60px; top: 178px; }
  .doctor__name { color: var(--sky); font-size: 21px; font-weight: 700; }
  .doctor__name small { font-size: 12px; font-weight: 400; margin-left: 4px; }
  .doctor__credential { color: var(--sky); font-size: 16px; line-height: 1.3; margin-top: 4px; }

  .social { position: absolute; left: 60px; top: 284px; display: flex; align-items: center; gap: 8px; color: var(--muted); font-size: 15px; }
  .social__dot { width: 16px; height: 16px; border-radius: 50%; background: var(--sky); }

  .contact { position: absolute; left: 400px; top: 220px; list-style: none; }
  .contact li { display: flex; align-items: center; gap: 14px; color: var(--muted); font-size: 17px; height: 28px; }
  .contact svg { width: 16px; height: 16px; fill: var(--sky); }

  .stripe { position: absolute; left: 0; top: 334px; width: 260px; height: 10px; background: var(--stripe); }
  .tab {
    position: absolute; left: 250px; right: 0; top: 334px; bottom: 0;
    background: linear-gradient(90deg, var(--sky), var(--sky-deep));
    border-top-left-radius: 40px;
    color: var(--white); font-size: 20px; letter-spacing: 1px;
    display: flex; align-items: center; justify-content: center;
  }
</style>
</head>
<body>
  <section class="card card--front">
    <div class="brand">
      <div class="brand__mark"></div>
      <div class="brand__name"><span class="primary">Moravel</span><span class="secondary">Aesthetic Doctor</span></div>
    </div>
    <p class="services">Dermal Injectables &nbsp;|&nbsp; Plasma Facials &nbsp;|&nbsp; Microneedling<br>Skin Boosters &nbsp;|&nbsp; Excessive Sweating</p>
    <div class="band">HOME AND SPA BASED TREATMENTS</div>
  </section>

  <section class="card card--back">
    <div class="brand">
      <div class="brand__mark"></div>
      <div class="brand__name"><span class="primary">Moravel</span><span class="secondary">Aesthetic Doctor</span></div>
    </div>
    <div class="doctor">
      <p class="doctor__name">Dr Elise Varrow<small>MRCPCH MD</small></p>
      <p class="doctor__credential">Australasian Diploma<br>of Aesthetic Medicine</p>
    </div>
    <div class="social">Follow us on: <span class="social__dot"></span><span class="social__dot"></span></div>
    <ul class="contact">
      <li><svg viewBox="0 0 24 24"><path d="M6.6 10.8a15.1 15.1 0 006.6 6.6l2.2-2.2a1 1 0 011-.25 11.4 11.4 0 003.6.57 1 1 0 011 1V20a1 1 0 01-1 1A17 17 0 013 4a1 1 0 011-1h3.5a1 1 0 011 1c0 1.25.2 2.45.57 3.57a1 1 0 01-.25 1z"/></svg>0800 484 317</li>
      <li><svg viewBox="0 0 24 24"><path d="M2 5h20v14H2z M3 6l9 7 9-7" fill="none" stroke="#52b3ea" stroke-width="2"/></svg>elise@moravel.co.nz</li>
      <li><svg viewBox="0 0 24 24"><circle cx="12" cy="12" r="9" fill="none" stroke="#52b3ea" stroke-width="2"/><path d="M3 12h18M12 3c3 3 3 15 0 18M12 3c-3 3-3 15 0 18" fill="none" stroke="#52b3ea" stroke-width="1.6"/></svg>www.moravel.co.nz</li>
    </ul>
    <div class="stripe"></div>
    <div class="tab">HOME AND SPA BASED TREATMENTS</div>
  </section>
</body>
</html>
```